Blood Testing Health App

We are looking for a graphics designer to create a web app for us so that we may insert it into a health management website system.
For branding purposes we are at www.Vantiqor.com and we are revamping our website... Example of new colors attached.
How we work...
We are a blood testing company based in the USA.
We offer a blood testing service nationwide in the USA.
We allow customers to order tests directly from us, visit a lab, have their blood drawn, or submit a urine sample, the lab tests it and they send the results back to our computer system and we share it with the customer.
The benefits of this are the customer does not need to go to the doctor and pay for the doctors visit to order these tests, which save them money. The tests are cheaper than going through the doctor. The customer simply uses us to get the test and the results and they can then take the results to their doctor... this process has saved them money. Others may be interested in regular check ups for blood work etc... and this allows them to do it with out needing a doctor, or if you have no insurance, this is a cheaper option too. We are quicker than a doctor, customers do not need appointments etc.
Hopefully you now have a better understanding as to what we do.
Here is the spec.
The app screen size is 750 px wide by 700 px high. ( A pdf is attached to show where the app is going to go, it is on page 3 of the pdf) The customer will have the ability to scroll… therefore the length of the page can be longer.
The app will consist of the following sections
Entry Page –
This will be the first page the user sees upon opening the app. This will be where they are directed from to the sections of the app discussed below. This needs to be branded for VantiQor with a modern look.
1 – Order Test (Giving them the ability to purchase a blood test within the app)
2 – VantiQor Dashboard (A dashboard that has everything they could need to use our service_
How it works Section on entry page – this will be a simple set of graphics showing how the service works. We already have the graphics for this, they do not need to be built again. They are attached to this brief
Basic structure of sections –
Order Test –
This page contains all tests, filed in categories – and Sub categories – Each test needs a link to an Information section – Price – Buy Now – Cart Process
VantiQor Dashboard –
A page of icons along the top of the app
- My Confirmation
- My Nearest Lab
- My Receipt
- My Orders
- My Account
- My Results
- My Inbox
- Contact Us
Sections in more detail -
Order A Test –
Show all categories/ sub categories – There are 23 categories, 14 sub categories, and within these categories are 300 tests - Here is the information for the categories etc - http://www.vantiqor.com/panels.aspx?PanelGroupID=4 Just in case it helps :)
We need to present this in a graphic format that is spacious, modern (brimlake, kivvo web appearance is the direction we are going for) We need it to be clear and not overwhelming to the customer.
Functionality idea…
Customer clicks category/ subcategory and tests appear.
Customer sees small 35 word description. For more information the test opens into a lightbox or expand the container which ever graphic designer believes to be most visually appealing
Buy Now must always be visible, along with price of the test
Buying process explained – Customer clicks buy now –
They are then taken to a Review Order screen ( This contains Order summary and choose payment method – insert payment details )
– Confirm payment –
Confirmation screen appears, thanking them.
They are then taken to the VantiQor Dashboard...
VantiQor Dashboard –
"My Confirmation" - Print Confirmation Order (PDF is in brief, we want this web based not a pdf download)
"My Nearest Lab Location" - This does not need to be designed because the web developer has this part under control, but we do need the icon in the dashboard
"My Receipt" - Print receipt - This does not exist in our system yet. So we need to create this from scratch - It will need to have - The test they are purchasing and the amount of the test - The customers name - The order ID - Must provide printer friendly option too
"My Orders" - This will have a list of orders - At the end of each order will be a status update of either "Test results" "Open order"
A graphic table format would be perfect. This will be linked to relevant results if they have been received. I have also attached a version of what the customer currently sees on our website. We know it is nasty ;) We are redesigning... but the information is there for this section to help design it with the right info. If the results are ready it will say in this list.
"Results Ready" will be a link to show those results once the customer has clicked the link, and the results will appear in the app, under the icons. There must be a printer friendly version too.
"My Results" Developer will sort this page out but we need the icon... It will be exactly like my orders but only show test results
"My Account" - This will be a place for them to update their personal information - Name, DOB, Address, Email Address
"My Inbox" - An inbox interface - Our way of contacting the customer for promotions we are running etc – We need a design of how this screen will appear. We also need the icon in the dashboard to have a notification on it if there are messages in the customers inbox. A little red 1, or circle with number of messages in the inbox.
"Customer Service" - This does not need to be designed because the web developer has this part under control, but we do need the icon in the dashboard
Icons appear along the top of app ( example - Mac icons/ iphone app icons) When the customer clicks an icon the content always appears below the icons
Here is more information for the icons and what should appear when each icon is clicked.
Screens to be designed –
Entry Page
Order A Test Page
Review Order Screen/Payment Screen - Show a lightbox that shows payment has been confirmed. Customer clicks close and are on the Confirmation Screen
VantiQor Dashboard - Screens mentioned in detail above
We can't wait to see your designs!
Please email any questions.
Hi all this is the first time we have used pixel harbor and understand the budget was too low for this project. We have now increased the budget to $2,000 and extended the deadline by another week
Hi all we are receiving some really great designs. I just added an example of the space that the web app will be going into... It is called "morvelapp.pdf"
Hi guys updated the brief. Hopefully this will help with the dashboard part of the design

```html
<!DOCTYPE html>
<html lang="en">
<head>
<meta charset="utf-8">
<title>VantiQor Dashboard – Panel Test Result</title>
<link href="https://fonts.googleapis.com/css2?family=Arimo:wght@400;700&display=swap" rel="stylesheet">
<style>
:root{
  --ink:#222;
  --ink-soft:#555;
  --muted:#888;
  --brand-green:#8cc63f;
  --brand-dark:#3a3a3a;
  --title-blue:#1e73be;
  --accent-orange:#f26522;
  --accent-orange-light:#ff7a33;
  --section-red:#ff5000;
  --badge-red:#e8352b;
  --band-top:#f4f4f4;
  --band-bottom:#dadada;
  --frame-grey:#e6e6e6;
  --rule:#dedede;
  --white:#fff;
}
*{box-sizing:border-box;margin:0;padding:0}
html,body{width:715px;height:1200px;overflow:hidden;background:var(--white)}
body{position:relative;font-family:"Arimo",Arial,sans-serif;color:var(--ink);font-size:12.5px;line-height:16px}

/* header */
.site-header{position:absolute;left:0;top:0;width:715px;height:97px;background:var(--white)}
.brand{position:absolute;left:17px;top:44px;display:flex;align-items:center;gap:8px}
.brand-name{font-size:37px;line-height:40px;font-weight:400;color:var(--brand-dark);letter-spacing:-0.5px}
.brand-mark{width:18px;height:18px;background:var(--brand-green)}
.top-tab{position:absolute;top:29px;width:118px;height:68px;text-align:center;font-size:10px;letter-spacing:.3px}
.top-tab svg{display:block;margin:12px auto 6px}
.tab-order{left:322px;color:#aaa}
.tab-dashboard{left:435px;background:#e9e9e9;color:var(--brand-green);border-radius:6px 6px 0 0}
.social{position:absolute;top:60px;display:flex;gap:11px;left:598px}
.social span{width:26px;height:26px;border-radius:50%;background:var(--brand-green)}

/* icon band */
.icon-band{position:absolute;left:0;top:97px;width:715px;height:128px;background:linear-gradient(var(--band-top),var(--band-bottom))}
.dash-nav{position:absolute;left:0;top:0;width:715px;height:128px}
.dash-item{position:absolute;top:18px;width:88px;margin-left:-44px;text-align:center;font-size:11.5px;line-height:12px;color:var(--ink)}
.dash-item.active{color:var(--title-blue)}
.dash-icon{display:block;width:60px;height:60px;margin:0 auto 4px;border-radius:50%;background:radial-gradient(circle at 50% 35%,#fff 0,#f0f0f0 55%,#cfcfcf 100%);box-shadow:0 2px 3px rgba(0,0,0,.25);border:1px solid #c8c8c8}
.dash-icon svg{display:block;margin:12px auto}
.badge{position:absolute;top:-2px;left:57px;min-width:22px;height:18px;border-radius:4px;background:var(--badge-red);color:var(--white);font-size:11px;line-height:18px;text-align:center}
.pointer{position:absolute;left:304px;top:120px;width:0;height:0;border-left:8px solid transparent;border-right:8px solid transparent;border-bottom:8px solid var(--white)}

/* result panel */
.result-frame{position:absolute;left:16px;top:250px;width:680px;height:906px;background:var(--frame-grey);border-radius:8px}
.result-title{position:absolute;left:20px;top:24px;font-size:23px;line-height:26px;font-weight:700;color:var(--title-blue)}
.actions{position:absolute;top:15px;left:389px;display:flex;gap:7px}
.action-btn{height:20px;padding:0 6px 0 12px;display:flex;align-items:center;gap:8px;border-radius:3px;background:linear-gradient(var(--accent-orange-light),var(--accent-orange));color:var(--white);font-size:9px;font-weight:700;box-shadow:0 1px 2px rgba(0,0,0,.3)}
.action-btn::after{content:"";width:11px;height:11px;border-radius:50%;border:1.5px solid var(--white)}
.btn-print{width:71px}.btn-pdf{width:118px}.btn-email{width:70px}
.result-sheet{position:absolute;left:15px;top:49px;width:647px;height:841px;background:var(--white);border-radius:8px}

.kv{display:grid;grid-template-columns:120px 12px 1fr}
.specimen{position:absolute;left:26px;top:19px;width:300px}
.account-extra{position:absolute;left:388px;top:19px;width:160px;text-align:right}
.patient-heading{position:absolute;left:26px;top:88px;font-size:16.5px;font-weight:700;line-height:20px}
.patient-left{position:absolute;left:26px;top:121px;width:320px}
.patient-left .kv{grid-template-columns:92px 17px 1fr}
.patient-right{position:absolute;left:378px;top:121px;width:270px}
.patient-right .kv{grid-template-columns:103px 17px 1fr}

.director{position:absolute;left:26px;top:285px;width:600px}
.director h3{font-size:12.5px;font-weight:700}
.orders{position:absolute;left:26px;top:384px;font-weight:700;line-height:22px}
.orders span{font-weight:400}

.results-table{position:absolute;left:15px;top:431px;width:617px;height:262px;border:1px solid var(--rule);border-radius:8px;overflow:hidden}
.row{display:grid;grid-template-columns:220px 67px 53px 74px 106px 1fr;padding-left:17px}
.row-head{height:29px;align-items:center;background:#f0f0f0;border-bottom:1px solid var(--rule);font-weight:700;color:#444}
.group{border-bottom:1px solid var(--rule);padding:10px 0 8px}
.group:last-child{border-bottom:none}
.group-title{padding-left:17px;color:var(--section-red);font-weight:700}
.note{display:grid;grid-template-columns:220px 1fr;padding-left:36px;color:var(--muted);font-size:12px;line-height:16px}
.note.first{margin-top:12px}

.lab-footer{position:absolute;left:15px;top:703px;width:617px;height:50px;background:#ececec;border-radius:3px;display:grid;grid-template-columns:130px 300px 1fr;padding:10px 0 0 17px}
.disclaimer{position:absolute;left:20px;top:775px;width:607px;text-align:center}
</style>
</head>
<body>

<header class="site-header">
  <div class="brand"><span class="brand-name">VantiQor</span><span class="brand-mark"></span></div>
  <div class="top-tab tab-order">
    <svg width="26" height="18" viewBox="0 0 26 18"><rect x="1" y="1" width="24" height="13" rx="2" fill="none" stroke="#bbb" stroke-width="2"/><rect x="0" y="15" width="26" height="3" fill="#bbb"/></svg>
    ORDER A TEST
  </div>
  <div class="top-tab tab-dashboard">
    <svg width="24" height="20" viewBox="0 0 24 20"><rect x="6" y="1" width="17" height="13" fill="none" stroke="#8cc63f" stroke-width="2"/><rect x="1" y="6" width="17" height="13" fill="#e9e9e9" stroke="#8cc63f" stroke-width="2"/></svg>
    DASHBOARD
  </div>
  <div class="social" aria-label="Social links"><span></span><span></span><span></span></div>
</header>

<section class="icon-band">
  <nav class="dash-nav">
    <div class="dash-item" style="left:45px"><span class="dash-icon" role="img" aria-label="Monitor icon"><svg width="34" height="34" viewBox="0 0 34 34"><rect x="3" y="4" width="28" height="20" rx="2" fill="#555"/><rect x="6" y="7" width="22" height="14" fill="#ddd"/><polyline points="7,14 12,14 14,10 17,18 19,14 27,14" fill="none" stroke="#555" stroke-width="1.5"/><rect x="14" y="24" width="6" height="5" fill="#555"/><rect x="9" y="29" width="16" height="2" fill="#555"/></svg></span>My Confirmation</div>
    <div class="dash-item" style="left:133px"><span class="dash-icon" role="img" aria-label="Lab microscope icon area"><svg width="34" height="34" viewBox="0 0 34 34"><circle cx="17" cy="17" r="11" fill="#666"/></svg></span>My<br>Nearest Lab</div>
    <div class="dash-item" style="left:222px"><span class="dash-icon" role="img" aria-label="DNA strand icon area"><svg width="34" height="34" viewBox="0 0 34 34"><circle cx="17" cy="17" r="11" fill="#666"/></svg></span>My Orders</div>
    <div class="dash-item active" style="left:312px"><span class="dash-icon" role="img" aria-label="Clipboard with heartbeat icon"><svg width="34" height="34" viewBox="0 0 34 34"><rect x="7" y="5" width="20" height="26" rx="2" fill="none" stroke="#1e73be" stroke-width="2.5"/><rect x="13" y="3" width="8" height="5" rx="1" fill="#1e73be"/><polyline points="10,19 14,19 16,14 19,24 21,19 24,19" fill="none" stroke="#1e73be" stroke-width="2"/></svg></span>My Results</div>
    <div class="dash-item" style="left:399px"><span class="dash-icon" role="img" aria-label="Receipt list icon"><svg width="34" height="34" viewBox="0 0 34 34"><rect x="7" y="4" width="20" height="27" rx="2" fill="none" stroke="#555" stroke-width="2.5"/><g fill="#555"><rect x="11" y="10" width="3" height="2"/><rect x="16" y="10" width="8" height="2"/><rect x="11" y="15" width="3" height="2"/><rect x="16" y="15" width="8" height="2"/><rect x="11" y="20" width="3" height="2"/><rect x="16" y="20" width="8" height="2"/><rect x="11" y="25" width="3" height="2"/><rect x="16" y="25" width="8" height="2"/></g></svg></span>My Receipts</div>
    <div class="dash-item" style="left:487px"><span class="dash-icon" role="img" aria-label="Account person icon area"><svg width="34" height="34" viewBox="0 0 34 34"><circle cx="17" cy="17" r="11" fill="#666"/></svg></span>My Account</div>
    <div class="dash-item" style="left:577px"><span class="dash-icon" role="img" aria-label="Envelope icon"><svg width="34" height="34" viewBox="0 0 34 34"><rect x="4" y="9" width="26" height="17" fill="#555"/><polyline points="4,9 17,19 30,9" fill="none" stroke="#ddd" stroke-width="1.5"/></svg></span>My Inbox<span class="badge">2</span></div>
    <div class="dash-item" style="left:665px"><span class="dash-icon" role="img" aria-label="Support agent icon area"><svg width="34" height="34" viewBox="0 0 34 34"><circle cx="17" cy="17" r="11" fill="#666"/></svg></span>Contact Us</div>
  </nav>
  <span class="pointer"></span>
</section>

<main class="result-frame">
  <h1 class="result-title">Panel Test Result</h1>
  <div class="actions">
    <span class="action-btn btn-print">PRINT</span>
    <span class="action-btn btn-pdf">DOWNLOAD PDF</span>
    <span class="action-btn btn-email">EMAIL</span>
  </div>

  <article class="result-sheet">
    <div class="specimen">
      <div class="kv"><span>Specimen Number</span><span>:</span><span>17961202890</span></div>
      <div class="kv"><span>Control #</span><span>:</span><span>34584</span></div>
      <div class="kv"><span>Account #</span><span>:</span><span>09359830</span></div>
    </div>
    <div class="account-extra">
      <div>Account Phone # :</div>
      <div>Route :</div>
    </div>

    <h2 class="patient-heading">Patient Information:</h2>
    <div class="patient-left">
      <div class="kv"><span>Last Name</span><span>:</span><span>Whitlock</span></div>
      <div class="kv"><span>First Name</span><span>:</span><span>Dana</span></div>
      <div class="kv"><span>Middle Name</span><span>:</span><span></span></div>
      <div class="kv"><span>Age</span><span>:</span><span>28</span></div>
      <div class="kv"><span>Date of Birth</span><span>:</span><span>09-11-1984</span></div>
      <div class="kv"><span>Sex</span><span>:</span><span>Female</span></div>
      <div class="kv"><span>Fasting</span><span>:</span><span></span></div>
      <div class="kv"><span>Address</span><span>:</span><span>1234 Any Street Harbor Point,<br>FL 33900</span></div>
    </div>
    <div class="patient-right">
      <div class="kv"><span>SSN#</span><span>:</span><span></span></div>
      <div class="kv"><span>Phone #</span><span>:</span><span>555-014-2290</span></div>
      <div class="kv"><span>Total Volume</span><span>:</span><span></span></div>
      <div class="kv"><span>Date Collected</span><span>:</span><span>9/23/2013 12:37:00 PM</span></div>
      <div class="kv"><span>Date Entered</span><span>:</span><span>9/24/2013 10:12:00 AM</span></div>
      <div class="kv"><span>Date Reported</span><span>:</span><span>9/28/2013 08:32:00 PM</span></div>
    </div>

    <section class="director">
      <h3>Medical Directors Comments</h3>
      <p>You have now taken the first step to being an active participant in your healthcare. These results are intended for informational purposes only. If you have further questions or concerns regarding your results please discuss with your healthcare provider. A helpful link to understanding your results can be found at http://www.labinsightguide.org</p>
    </section>

    <div class="orders">
      <div>Tests Ordered : <span>Glucose, Serum; Hgb A1c with eAG Estimation;</span></div>
      <div>General Comments :</div>
    </div>

    <section class="results-table">
      <div class="row row-head"><span>Tests</span><span>Results</span><span>Flags</span><span>Units</span><span>Ref. Interval</span><span>Lab</span></div>
      <div class="group">
        <div class="group-title">Glucose, Serum</div>
        <div class="row"><span>Glucose, Serum</span><span>90</span><span>N</span><span>mg/dL</span><span>65-99</span><span>001032</span></div>
      </div>
      <div class="group">
        <div class="group-title">Hgb A1c with eAG Estimation</div>
        <div class="row"><span>Hemoglobin A1c</span><span>5.3</span><span>N</span><span>%</span><span>4.8-5.6</span><span>001464</span></div>
        <div class="note first"><span>Increased risk for diabetes:</span><span style="color:var(--ink)">5.7 - 6.4</span></div>
        <div class="note"><span>Diabetes:</span><span style="color:var(--ink)">&gt;6.4</span></div>
        <div class="note"><span>Glycemic control for adults<br>with diabetes:</span><span style="color:var(--ink);align-self:end">&lt;7.0</span></div>
      </div>
      <div class="group" style="padding-top:12px">
        <div class="row"><span>Estim. Avg Glu (eAG)</span><span>105</span><span>N</span><span>mg/dL</span><span></span><span>001471</span></div>
      </div>
    </section>

    <footer class="lab-footer">
      <span>DV</span>
      <span>Northvale Diagnostics Denver<br>2176 Cedar Ridge Road, Englewood, CO</span>
      <span>PhD Aaron Lisle</span>
    </footer>

    <p class="disclaimer">These lab results are for information only. They are not intended for diagnosis or treatment. Please feel free to discuss your results with your healthcare provider.</p>
  </article>
</main>

</body>
</html>
```